UX Design for Analytics Web Application

http://velqoranthe.com/
We are tech & consulting company with analytics products (web applications), located at Rio de Janeiro, Brazil.

We are searching a partner do develop UX for our products, i.e, aesthetics, usability, HTML/CSS.

Currently we have a product suite and the goal is to make a pilot re-design project with one of our products.

The product of interest is interactive webapp that aims at data analysis, significantly different from blogs, e-commerce or landing pages.

We do have a software development team but we lack an UX & HTML expert. Currently we use Bootstrap templates but the results are insatisfatory.

So, the project scope is, to develop the arts (UX, aesthetics, etc) along with the code/mockup (HTML/CSS) for one of our product (3 pages).

This is a pilot project and there's potential to rehire for our other products. Code quality is of importance.

More details and specification can be found in attached files.

Target Market(s)

Executives, managers & consultants

Industry/Entity Type

It Company

Coding

Coded - Design and coding required

Number of Pages Required

3 page

Font styles to use
Sans Serif

Requirements
Must have
• (see attached files, prefer the pptx version))
• -Responsive
Nice to have
• (see attached files, prefer the pptx version)
Should not have
• -Avoid Green, Red and Yellow colors. They have a meaning of good, bad and average in our products.

```html
<!DOCTYPE html>
<html lang="pt">
<head>
<meta charset="utf-8">
<title>Velqoranthe – Ajuste de Lacuna</title>
<link rel="stylesheet" href="https://fonts.googleapis.com/css2?family=Open+Sans:wght@400;600;700&display=swap">
<style>
:root{
  --ink:#333;
  --navy:#1e2333;
  --slate:#3f4e66;
  --sky:#4dbbf5;
  --panel:#e8e8e8;
  --line:#dcdcdc;
  --muted:#666;
  --white:#fff;
  --green-a:#76d62a;
  --green-b:#1e6e0c;
}
*{box-sizing:border-box;margin:0;padding:0}
html,body{width:1200px;height:1124px;overflow:hidden}
body{font-family:"Open Sans",Arial,sans-serif;color:var(--ink);background:var(--white);position:relative}

/* header */
.topbar{position:absolute;left:0;top:0;width:1200px;height:128px;border-bottom:1px solid var(--line)}
.menu-btn{position:absolute;left:24px;top:52px;width:28px;height:22px;display:flex;flex-direction:column;justify-content:space-between}
.menu-btn span{height:4px;background:var(--ink);border-radius:1px}
.brand{position:absolute;left:132px;top:30px;display:flex;align-items:center;gap:10px}
.brand-dot{width:40px;height:40px;border-radius:50%;background:var(--ink)}
.brand-name{font-size:34px;font-weight:700;color:var(--ink);letter-spacing:-0.5px;line-height:44px}
.brand-tag{position:absolute;left:198px;top:80px;font-size:12.5px;line-height:16px;color:var(--ink)}
.tool{position:absolute;top:44px;width:40px;height:40px;border-radius:50%;background:var(--ink)}
.tool svg{position:absolute;left:10px;top:10px;width:20px;height:20px;fill:var(--white)}
.badge{position:absolute;left:874px;top:44px;width:20px;height:20px;border-radius:50%;background:var(--sky);color:var(--white);font-size:9px;text-align:center;line-height:20px}

/* layout */
.board{position:absolute;left:132px;top:146px;width:936px;height:886px;background:var(--panel)}
.card{position:absolute;left:148px;width:904px;background:var(--white)}
.card-head{height:56px;border-bottom:1px solid var(--line);position:relative}
.card-title{position:absolute;left:16px;top:17px;font-size:14.5px;font-weight:400;color:#222}
.collapse{position:absolute;right:16px;top:20px;width:12px;height:12px;border:1.5px solid #222;border-radius:2px}
.collapse::after{content:"";position:absolute;left:2px;right:2px;top:4px;height:1.5px;background:#222}

/* gauge & table */
.gauge{position:absolute;left:164px;top:256px}
.gap-table{position:absolute;left:380px;top:242px;width:656px;height:137px;background:var(--slate);padding:8px;font-size:10.5px}
.gap-head,.gap-row{display:grid;grid-template-columns:160px 184px 160px 1fr;align-items:center;padding-left:22px}
.gap-head{height:38px;background:var(--navy);color:var(--sky);font-size:11px}
.gap-row{height:38px;background:var(--white);color:var(--muted);margin-top:4px}

/* budget */
.field-label{position:absolute;left:166px;font-size:12px;color:#333}
.field{position:absolute;left:166px;width:220px;height:35px;border:1px solid #ccc;border-radius:2px;font-size:11px;text-align:right;padding-right:15px;line-height:33px}
.kpi{position:absolute;top:502px;height:124px}
.kpi-bar{position:absolute;left:0;top:0;width:32px;height:124px;background:var(--slate)}
.kpi-fill{position:absolute;left:0;bottom:0;width:32px;background:var(--sky)}
.kpi-label{position:absolute;left:41px;top:76px;font-size:14.5px;color:var(--muted)}
.kpi-value{position:absolute;left:41px;top:92px;font-size:29px;color:var(--slate);white-space:nowrap;line-height:36px}

/* seasonality */
.remain{position:absolute;left:166px;top:758px;font-size:9px;color:#222}
.remain-bar{position:absolute;left:166px;top:775px;width:868px;height:11px;border:1px solid #bbb;border-radius:6px}
.month{position:absolute;top:808px;width:60px;margin-left:-30px;text-align:center;font-size:9.5px;color:#222}
.slider{position:absolute;top:827px;width:8px;height:115px;margin-left:-4px;background:var(--slate)}
.slider .fill{position:absolute;left:0;bottom:0;width:8px;background:var(--sky)}
.slider .knob{position:absolute;left:-3px;width:14px;height:14px;margin-top:-7px;border-radius:50%;background:var(--navy);border:3px solid var(--navy)}
.slider .knob::after{content:"";position:absolute;left:1px;top:1px;width:6px;height:6px;border-radius:50%;background:var(--sky)}
.slider .ticks{position:absolute;left:12px;top:0;width:2px;height:115px;background:repeating-linear-gradient(to bottom,#999 0 1px,transparent 1px 6px)}
.share{position:absolute;top:954px;width:34px;height:24px;margin-left:-17px;border:1px solid #ccc;font-size:8.5px;text-align:center;line-height:22px;color:#333}
.amount{position:absolute;top:982px;width:40px;margin-left:-20px;text-align:center;font-size:8.5px;color:#333}

/* footer */
.footer{position:absolute;left:0;top:1068px;width:1200px;height:56px;background:#e6e6e6;text-align:center;font-size:11px;line-height:56px;color:#333}
</style>
</head>
<body>

<header class="topbar">
  <div class="menu-btn"><span></span><span></span><span></span></div>
  <div class="brand"><span class="brand-dot"></span><span class="brand-name">Velqoranthe</span></div>
  <div class="brand-tag">Business Intelligence,<br>Planning &amp; Strategy</div>
  <div class="tool" style="left:883px"><svg viewBox="0 0 20 20"><path d="M10 2a1.5 1.5 0 0 1 1.5 1.5v.6A5 5 0 0 1 15 9v4l2 2v1H3v-1l2-2V9a5 5 0 0 1 3.5-4.9v-.6A1.5 1.5 0 0 1 10 2zm-2 15h4a2 2 0 0 1-4 0z"/></svg></div>
  <div class="badge">0</div>
  <div class="tool" style="left:955px"><svg viewBox="0 0 20 20"><circle cx="10" cy="6" r="3.5"/><path d="M3 17c0-4 3-6 7-6s7 2 7 6z"/></svg></div>
  <div class="tool" style="left:1027px"><svg viewBox="0 0 20 20"><path d="M8.6 2h2.8l.4 2.2 1.6.9 2.1-.8 1.4 2.4-1.7 1.5v1.6l1.7 1.5-1.4 2.4-2.1-.8-1.6.9-.4 2.2H8.6l-.4-2.2-1.6-.9-2.1.8-1.4-2.4 1.7-1.5V8.2L3.1 6.7l1.4-2.4 2.1.8 1.6-.9zM10 7.5a2.5 2.5 0 1 0 0 5 2.5 2.5 0 0 0 0-5z"/></svg></div>
</header>

<main>
  <div class="board"></div>

  <!-- gap adjustment -->
  <section class="card" style="top:162px;height:238px">
    <div class="card-head"><h2 class="card-title">Ajuste de Lacuna</h2><span class="collapse"></span></div>
  </section>
  <svg class="gauge" width="192" height="100" viewBox="0 0 192 100" aria-label="Indicador 100">
    <defs><linearGradient id="gaugeFill" x1="0" x2="1"><stop offset="0" stop-color="#76d62a"/><stop offset="1" stop-color="#1e6e0c"/></linearGradient></defs>
    <path d="M1 94A93 93 0 0 1 187 94H155A61 61 0 0 0 33 94z" fill="url(#gaugeFill)"/>
    <text x="94" y="92" text-anchor="middle" font-family="Open Sans,Arial,sans-serif" font-weight="700" font-size="30" fill="#2d8a12">100</text>
    <rect x="144" y="76" width="46" height="17" rx="8" fill="#bbb" stroke="#888"/>
    <rect x="160" y="79" width="14" height="11" fill="#eee"/>
  </svg>
  <div class="gap-table">
    <div class="gap-head"><span></span><span>Lacuna R$ (Lacuna %)</span><span>Valor Analisado</span><span>Valor Otimizado</span></div>
    <div class="gap-row"><span>Valores Ajustados</span><span>6,500,00 (21.67%)</span><span>30,00a0,00</span><span>23,500,00</span></div>
    <div class="gap-row"><span>Valores Ajustados</span><span>6,500,00 (21.67%)</span><span>6,500,00 (21.67%)</span><span>23,500,00</span></div>
  </div>

  <!-- budget -->
  <section class="card" style="top:418px;height:238px">
    <div class="card-head"><h2 class="card-title">Orcamento para os Proximos 12 Meses</h2><span class="collapse"></span></div>
  </section>
  <label class="field-label" style="top:499px">Inflation</label>
  <div class="field" style="top:519px">10 %</div>
  <label class="field-label" style="top:571px">Growth</label>
  <div class="field" style="top:591px">10 %</div>

  <div class="kpi" style="left:434px"><div class="kpi-bar"><div class="kpi-fill" style="height:100px"></div></div><div class="kpi-label">ORCAMENTO</div><div class="kpi-value">45.900,00</div></div>
  <div class="kpi" style="left:653px"><div class="kpi-bar"><div class="kpi-fill" style="height:76px"></div></div><div class="kpi-label">META</div><div class="kpi-value">35.955,00</div></div>
  <div class="kpi" style="left:870px"><div class="kpi-bar"><div class="kpi-fill" style="height:20px"></div></div><div class="kpi-label">GANHO</div><div class="kpi-value">9.945,00</div></div>

  <!-- seasonality -->
  <section class="card" style="top:674px;height:342px">
    <div class="card-head"><h2 class="card-title">Sazonalidade para os Proximos 12 Meses</h2><span class="collapse"></span></div>
  </section>
  <div class="remain">Lacuna sobrando : 0.0%</div>
  <div class="remain-bar"></div>

  <div class="month" style="left:183px">Jan</div><div class="slider" style="left:183px"><div class="fill" style="height:37px"></div><div class="knob" style="top:78px"></div><div class="ticks"></div></div><div class="share" style="left:183px">8.3%</div><div class="amount" style="left:183px">2.98</div>
  <div class="month" style="left:259px">Feb</div><div class="slider" style="left:259px"><div class="fill" style="height:21px"></div><div class="knob" style="top:94px"></div><div class="ticks"></div></div><div class="share" style="left:259px">8.3%</div><div class="amount" style="left:259px">2.98</div>
  <div class="month" style="left:335px">Mar</div><div class="slider" style="left:335px"><div class="fill" style="height:29px"></div><div class="knob" style="top:86px"></div><div class="ticks"></div></div><div class="share" style="left:335px">8.3%</div><div class="amount" style="left:335px">2.98</div>
  <div class="month" style="left:410px">Apr</div><div class="slider" style="left:410px"><div class="fill" style="height:53px"></div><div class="knob" style="top:62px"></div><div class="ticks"></div></div><div class="share" style="left:410px">8.3%</div><div class="amount" style="left:410px">2.98</div>
  <div class="month" style="left:486px">May</div><div class="slider" style="left:486px"><div class="fill" style="height:85px"></div><div class="knob" style="top:30px"></div><div class="ticks"></div></div><div class="share" style="left:486px">8.3%</div><div class="amount" style="left:486px">2.98</div>
  <div class="month" style="left:562px">Jun</div><div class="slider" style="left:562px"><div class="fill" style="height:13px"></div><div class="knob" style="top:102px"></div><div class="ticks"></div></div><div class="share" style="left:562px">8.3%</div><div class="amount" style="left:562px">2.98</div>
  <div class="month" style="left:638px">Jul</div><div class="slider" style="left:638px"><div class="fill" style="height:4px"></div><div class="knob" style="top:111px"></div><div class="ticks"></div></div><div class="share" style="left:638px">8.3%</div><div class="amount" style="left:638px">2.98</div>
  <div class="month" style="left:714px">Aug</div><div class="slider" style="left:714px"><div class="fill" style="height:7px"></div><div class="knob" style="top:108px"></div><div class="ticks"></div></div><div class="share" style="left:714px">8.3%</div><div class="amount" style="left:714px">2.98</div>
  <div class="month" style="left:790px">Sep</div><div class="slider" style="left:790px"><div class="fill" style="height:29px"></div><div class="knob" style="top:86px"></div><div class="ticks"></div></div><div class="share" style="left:790px">8.3%</div><div class="amount" style="left:790px">2.98</div>
  <div class="month" style="left:866px">Oct</div><div class="slider" style="left:866px"><div class="fill" style="height:29px"></div><div class="knob" style="top:86px"></div><div class="ticks"></div></div><div class="share" style="left:866px">8.3%</div><div class="amount" style="left:866px">2.98</div>
  <div class="month" style="left:942px">Nov</div><div class="slider" style="left:942px"><div class="fill" style="height:37px"></div><div class="knob" style="top:78px"></div><div class="ticks"></div></div><div class="share" style="left:942px">8.3%</div><div class="amount" style="left:942px">2.98</div>
  <div class="month" style="left:1018px">Dec</div><div class="slider" style="left:1018px"><div class="fill" style="height:45px"></div><div class="knob" style="top:70px"></div><div class="ticks"></div></div><div class="share" style="left:1018px">8.3%</div><div class="amount" style="left:1018px">2.98</div>
</main>

<footer class="footer">Copyright &nbsp;©&nbsp; 2017 &nbsp;Company name. &nbsp;All rights reserved.</footer>

</body>
</html>
```